Local Roofing/Construction company business needs new biz card design

We need a new business card design, current cards are from the start of this operation and generic at best. We are a local Construction Company (General Contractor) with a majority of our work originating from insurance claims-exterior finish work is the main focus (Roofs-Siding-Gutters etc). Heavily involved with homeowners and the low ball offers they receive from insurance company's after a insurable event takes place. I have attached some of our original logo file(s) below.

```html
<!DOCTYPE html>
<html lang="en">
<head>
<meta charset="utf-8">
<title>Northvale Builders – Business Card</title>
<link href="https://fonts.googleapis.com/css2?family=Open+Sans:wght@400;600;700&display=swap" rel="stylesheet">
<style>
  :root {
    --page-bg: #1b1c1f;
    --card-bg: #061d20;
    --card-bg-raised: #0c2c2b;
    --watermark: #0f2f2c;
    --brand-green: #4fbf6b;
    --text-white: #f2f5f3;
    --text-soft: #d9e2de;
  }
  * { box-sizing: border-box; margin: 0; padding: 0; }
  html, body {
    width: 1200px; height: 780px; overflow: hidden;
    background: var(--page-bg);
    font-family: "Open Sans", Arial, sans-serif;
  }
  .card-sheet {
    width: 1200px; height: 780px;
    display: flex; align-items: center; justify-content: center; gap: 40px;
  }
  .card {
    position: relative;
    width: 560px; height: 320px;
    background: var(--card-bg);
    border-radius: 22px;
    border-bottom: 4px solid var(--brand-green);
    border-right: 2px solid var(--brand-green);
    overflow: hidden;
  }

  /* Back side */
  .card--back { display: flex; align-items: center; justify-content: center; }
  .back-wordmark {
    display: flex; align-items: center; gap: 16px;
    color: var(--card-bg-raised);
    font-weight: 700; font-size: 36px; letter-spacing: 2px;
    text-transform: uppercase; white-space: nowrap;
  }
  .back-wordmark .mark-square {
    width: 42px; height: 42px; background: var(--card-bg-raised);
  }

  /* Front side */
  .front-watermark {
    position: absolute; left: 340px; top: 50px;
    width: 190px; height: 190px;
    background: var(--watermark);
  }
  .front-brand {
    position: absolute; left: 34px; top: 30px;
    display: flex; align-items: center; gap: 10px;
    color: var(--brand-green);
    font-weight: 700; font-size: 18px; letter-spacing: 1.5px; text-transform: uppercase;
    white-space: nowrap;
  }
  .front-brand .mark-square { width: 24px; height: 24px; background: var(--brand-green); }

  .front-contact { position: absolute; left: 34px; top: 90px; }
  .person-name { color: var(--brand-green); font-weight: 700; font-size: 24px; line-height: 1.1; }
  .person-role { color: var(--text-white); font-weight: 600; font-size: 13px; margin-top: 2px; }
  .address { color: var(--text-soft); font-size: 12px; line-height: 1.35; margin-top: 12px; }
  .contact-list { list-style: none; margin-top: 12px; }
  .contact-list li {
    display: flex; align-items: center; gap: 8px;
    color: var(--text-soft); font-size: 12px; line-height: 1.6; white-space: nowrap;
  }
  .contact-list svg { width: 12px; height: 12px; fill: var(--brand-green); flex: none; }

  .name-tab {
    position: absolute; right: 0; top: 96px;
    display: flex; align-items: stretch;
  }
  .name-tab__text { text-align: right; padding-right: 10px; white-space: nowrap; }
  .name-tab__name { font-weight: 700; font-size: 22px; line-height: 1.1; }
  .name-tab__name .first { color: var(--brand-green); }
  .name-tab__name .last { color: var(--text-white); }
  .name-tab__role { color: var(--text-white); font-size: 12px; margin-top: 2px; }
  .name-tab__bar { width: 34px; background: var(--brand-green); }
</style>
</head>
<body>
<main class="card-sheet">

  <section class="card card--back" aria-label="Card back">
    <div class="back-wordmark"><span class="mark-square"></span>Northvale Builders</div>
  </section>

  <section class="card card--front" aria-label="Card front">
    <span class="front-watermark" aria-hidden="true"></span>

    <div class="front-brand"><span class="mark-square"></span>Northvale Builders</div>

    <div class="front-contact">
      <p class="person-name">Mara Lindqvist</p>
      <p class="person-role">Co-Founder</p>
      <p class="address">48 Cedar Hollow<br>Rd, Brookfield, MO 63400</p>
      <ul class="contact-list">
        <li><svg viewBox="0 0 24 24" aria-hidden="true"><path d="M6.6 10.8a15 15 0 0 0 6.6 6.6l2.2-2.2a1 1 0 0 1 1-.25 11.4 11.4 0 0 0 3.6.57 1 1 0 0 1 1 1V20a1 1 0 0 1-1 1A17 17 0 0 1 3 4a1 1 0 0 1 1-1h3.5a1 1 0 0 1 1 1c0 1.25.2 2.45.57 3.57a1 1 0 0 1-.25 1z"/></svg>555-210-4478</li>
        <li><svg viewBox="0 0 24 24" aria-hidden="true"><path d="M6.6 10.8a15 15 0 0 0 6.6 6.6l2.2-2.2a1 1 0 0 1 1-.25 11.4 11.4 0 0 0 3.6.57 1 1 0 0 1 1 1V20a1 1 0 0 1-1 1A17 17 0 0 1 3 4a1 1 0 0 1 1-1h3.5a1 1 0 0 1 1 1c0 1.25.2 2.45.57 3.57a1 1 0 0 1-.25 1z"/></svg>555-210-9032 (Emergency)</li>
        <li><svg viewBox="0 0 24 24" aria-hidden="true"><path d="M12 2a10 10 0 1 0 0 20 10 10 0 0 0 0-20zm6.9 6h-2.9a15.7 15.7 0 0 0-1.4-3.6A8 8 0 0 1 18.9 8zM12 4c.8 1.2 1.5 2.5 1.9 4h-3.8c.4-1.5 1.1-2.8 1.9-4zM4.3 14a8 8 0 0 1 0-4h3.4a16 16 0 0 0 0 4zm.8 2h2.9c.3 1.3.8 2.5 1.4 3.6A8 8 0 0 1 5.1 16zM8 8H5.1a8 8 0 0 1 4.3-3.6C8.8 5.5 8.3 6.7 8 8zm4 12c-.8-1.2-1.5-2.5-1.9-4h3.8c-.4 1.5-1.1 2.8-1.9 4zm2.3-6H9.7a14.7 14.7 0 0 1 0-4h4.6a14.7 14.7 0 0 1 0 4zm.3 5.6c.6-1.1 1.1-2.3 1.4-3.6h2.9a8 8 0 0 1-4.3 3.6zM16.3 14a16 16 0 0 0 0-4h3.4a8 8 0 0 1 0 4z"/></svg>www.northvalebuilders.com</li>
        <li><svg viewBox="0 0 24 24" aria-hidden="true"><path d="M3 5h18a1 1 0 0 1 1 1v12a1 1 0 0 1-1 1H3a1 1 0 0 1-1-1V6a1 1 0 0 1 1-1zm9 7.2L4.4 7H4v.8l8 5.4 8-5.4V7h-.4z"/></svg>hello@northvalebuilders.com</li>
      </ul>
    </div>

    <div class="name-tab">
      <div class="name-tab__text">
        <p class="name-tab__name"><span class="first">Mara</span> <span class="last">Lindqvist</span></p>
        <p class="name-tab__role">Managing Director</p>
      </div>
      <span class="name-tab__bar"></span>
    </div>
  </section>

</main>
</body>
</html>
```